Business Card Design - ChoiceCraft

Looking for creative, modern design, two sided for ChoiceCraft that is consistent with color and feel of website www.choicecraftpro.net.
Updates

Back of card will be used to promote products or have a quote revolving around decisions, change, leadership, innovation, creativity. Back should also have space to promote website, but optional to use the icon. Front of the card will need to use the icon and have standard place for name, job title, phone and email. We are not looking to put a mailing address or fax. Also want space to place a few words/phrase explaining what we do...such as individual growth and organizational development or tools, training, information...in addition, want the facebook icon small on the front somewhere as we are also on facebook.

Vector file uploaded of icon.

Target Market(s)

Professional coaching for individual growth and organizational development

Industry/Entity Type

Business

Requirements
Must have
• Icon...see attached.

```html
<!DOCTYPE html>
<html lang="en">
<head>
<meta charset="utf-8">
<title>ChoiceCraft – Business Card</title>
<link rel="stylesheet" href="https://fonts.googleapis.com/css2?family=Open+Sans:wght@400;600;700&family=Arimo:wght@400;700&display=swap">
<style>
  :root {
    --stage: #1d1f22;
    --card-white: #ffffff;
    --blue-deep: #0a66b3;
    --blue-mid: #1a8fd6;
    --blue-light: #39c0f0;
    --blue-glow: #4fd0fa;
    --divider: #c9d3dc;
    --ink: #2b2b2b;
    --ink-soft: #4a4a4a;
    --white: #ffffff;
    --silver: #c9ccd0;
    --silver-dark: #8d9197;
  }
  * { box-sizing: border-box; margin: 0; padding: 0; }
  html, body { width: 1200px; height: 763px; overflow: hidden; }
  body {
    background: var(--stage);
    font-family: "Open Sans", Arial, sans-serif;
    position: relative;
  }
  .card {
    position: absolute;
    top: 222px;
    width: 540px;
    height: 318px;
    border-radius: 30px;
    overflow: hidden;
  }
  /* Front */
  .card-front { left: 40px; display: flex; background: var(--card-white); }
  .front-brand {
    width: 262px;
    position: relative;
    border-right: 3px solid var(--divider);
  }
  .brand-mark {
    position: absolute; top: 52px; left: 50%; transform: translateX(-50%);
    display: flex; flex-direction: column; align-items: center; gap: 14px;
  }
  .brand-dot {
    width: 96px; height: 96px; border-radius: 50%;
    background: var(--blue-mid);
  }
  .brand-name {
    font-size: 22px; font-weight: 400; color: var(--ink); letter-spacing: 0.2px;
  }
  .tagline {
    position: absolute; left: 30px; bottom: 34px;
    font-size: 14.5px; line-height: 1.3; color: var(--ink-soft);
  }
  .front-contact {
    flex: 1;
    background: linear-gradient(180deg, var(--blue-deep) 0%, var(--blue-mid) 55%, var(--blue-light) 100%);
    color: var(--white);
    padding: 50px 0 0 36px;
  }
  .person-name { font-size: 19px; font-weight: 700; }
  .person-title { font-size: 14px; margin-top: 2px; }
  .contact-list { list-style: none; margin-top: 30px; font-size: 13.5px; line-height: 1.35; }
  .contact-list li { display: flex; align-items: center; gap: 7px; }
  .contact-list svg { width: 11px; height: 11px; flex: none; }
  .social-dot { width: 9px; height: 9px; border-radius: 50%; background: var(--white); flex: none; margin: 0 1px; }
  /* Back */
  .card-back {
    left: 620px;
    background: radial-gradient(ellipse at 45% 45%, var(--blue-glow) 0%, var(--blue-mid) 38%, var(--blue-deep) 100%);
    color: var(--white);
    font-family: "Arimo", Arial, sans-serif;
    padding: 34px 26px 0 28px;
  }
  .quote { font-size: 14px; line-height: 1.25; margin-bottom: 6px; }
  .quote q { quotes: "\201C" "\201D"; }
  .quote q::before, .quote q::after { font-size: 20px; font-weight: 700; vertical-align: -4px; padding: 0 2px; }
  .quote cite { display: block; font-style: normal; font-weight: 700; margin-left: 12px; }
  .back-mark {
    position: absolute; right: 34px; bottom: 26px;
    display: flex; flex-direction: column; align-items: center; gap: 6px;
  }
  .back-dot {
    width: 82px; height: 82px; border-radius: 50%;
    background: radial-gradient(circle at 40% 35%, var(--silver) 0%, var(--silver-dark) 100%);
  }
  .back-name { font-size: 12px; font-weight: 700; color: var(--white); }
</style>
</head>
<body>
  <section class="card card-front" aria-label="Card front">
    <div class="front-brand">
      <div class="brand-mark">
        <span class="brand-dot"></span>
        <span class="brand-name">ChoiceCraft</span>
      </div>
      <p class="tagline">Supporting individual growth<br>&amp; organizational&nbsp; development</p>
    </div>
    <div class="front-contact">
      <h1 class="person-name">Your Name</h1>
      <p class="person-title">Title</p>
      <ul class="contact-list">
        <li><svg viewBox="0 0 12 12"><path d="M3 1l2 2.5-1.2 1.3c.6 1.3 1.6 2.3 2.9 2.9L8 6.5 10.5 8.5 9.5 10.5C5 10.5 1.5 7 1.5 2.5z" fill="#fff"/></svg>123-456-789</li>
        <li><svg viewBox="0 0 12 12"><rect x="1" y="2.5" width="10" height="7" rx="1" fill="#fff"/><path d="M1.5 3l4.5 3.5L10.5 3" stroke="#1a8fd6" stroke-width="1" fill="none"/></svg>info@choicecraftpro.net</li>
        <li><svg viewBox="0 0 12 12"><circle cx="6" cy="6" r="4.8" fill="none" stroke="#fff" stroke-width="1.1"/><path d="M1.2 6h9.6M6 1.2c-2.4 2.6-2.4 7 0 9.6M6 1.2c2.4 2.6 2.4 7 0 9.6" stroke="#fff" stroke-width=".9" fill="none"/></svg>www.choicecraftpro.net</li>
        <li><span class="social-dot"></span>/choicecraftpro</li>
      </ul>
    </div>
  </section>

  <section class="card card-back" aria-label="Card back">
    <p class="quote"><q>Try not to become a man of success, but rather a man of value.</q><cite>- Alden Ferris</cite></p>
    <p class="quote"><q>The only constant is change.</q><cite>- Theron Vale</cite></p>
    <p class="quote"><q>We are what we repeatedly do. Excellence is not an act, it is a habit.</q><cite>- Castor Lyne</cite></p>
    <p class="quote"><q>Simplicity is the ultimate sophistication.</q><cite>- Lorenzo Vanti</cite></p>
    <p class="quote"><q>Life is not fair - get used to it.</q><cite>- Wes Hartley</cite></p>
    <div class="back-mark">
      <span class="back-dot"></span>
      <span class="back-name">ChoiceCraft</span>
    </div>
  </section>
</body>
</html>
```